Business card for Luxury Portable Restroom Trailer company

We are a Luxury Portable Restroom Trailer Company Called FALCRIDGE HIRES. Based in Orange County California. We provide portable restroom trailers for events, such as, Weddings, Concerts, Charity events, Sporting events, Tournaments, Corporate events, ect. We rent and Sell the Luxury restrooms. Our colors are white, grey, and Orange. As you will see in the logo we uploaded.
There are 2 people in the company so the names and titles will change for the 3 people but card will remain the same. Here is the information for each Person: Dwight Penner CFO 555 318-0476
next Person: Leon Marchetti VP 555 318-0476
Next Person: Owen Marchetti CEO 555 318-0476
Information to include on the card: Luxury Restroom Trailers Rental and Sales. Weddings, Concerts, Charity, Sporting and Corp. Events.

```html
<!DOCTYPE html>
<html lang="en">
<head>
<meta charset="utf-8">
<title>Falcridge Hires – Business Card</title>
<link href="https://fonts.googleapis.com/css2?family=Arimo:wght@400;700&display=swap" rel="stylesheet">
<style>
  :root {
    --bg: #e9e7e4;
    --card-dark: #545456;
    --card-light: #ffffff;
    --mark-grey: #5a5a5c;
    --orange: #e8651e;
    --ink: #3a3a3a;
    --white: #ffffff;
  }
  * { margin: 0; padding: 0; box-sizing: border-box; }
  html, body {
    width: 1200px; height: 960px; overflow: hidden;
    background: var(--bg);
    font-family: "Arimo", Arial, sans-serif;
  }
  .card {
    position: absolute;
    width: 630px; height: 360px;
    border-radius: 22px;
    overflow: hidden;
    box-shadow: 0 10px 28px rgba(0,0,0,.18);
  }
  .card-front {
    left: 70px; top: 90px;
    background: var(--card-dark);
    color: var(--white);
    display: flex; flex-direction: column; align-items: center; justify-content: center;
  }
  .brand-name {
    font-weight: 700;
    font-size: 52px;
    letter-spacing: 2px;
    color: var(--white);
    line-height: 1;
  }
  .tagline {
    margin-top: 54px;
    text-align: center;
    font-size: 15px;
    line-height: 1.45;
    color: var(--white);
  }
  .card-back {
    left: 500px; top: 510px;
    background: var(--card-light);
    color: var(--ink);
  }
  .brand-mark-area {
    position: absolute; left: 0; bottom: 0;
    width: 330px; height: 300px;
    background: var(--mark-grey);
    border-top-right-radius: 160px;
  }
  .person {
    position: absolute; right: 40px; top: 40px; text-align: right;
  }
  .person-name {
    font-weight: 700; font-size: 24px; color: var(--orange); letter-spacing: .5px;
  }
  .person-title { font-size: 15px; color: var(--ink); margin-top: 2px; }
  .address {
    position: absolute; right: 40px; top: 140px; text-align: right;
    font-size: 15px; line-height: 1.4;
  }
  .contacts {
    position: absolute; right: 40px; top: 210px; list-style: none;
    font-size: 15px; line-height: 1.55; text-align: right;
  }
  .contacts li { display: flex; align-items: center; justify-content: flex-end; gap: 8px; }
  .contacts svg { width: 14px; height: 14px; fill: var(--orange); }
</style>
</head>
<body>
  <section class="card card-front">
    <div class="brand-name">FALCRIDGE HIRES</div>
    <p class="tagline">Luxury Restroom Trailers Rental and Sales<br>Weddings, Concerts, Charity, Sporting and Corp Events</p>
  </section>

  <section class="card card-back">
    <div class="brand-mark-area" role="img" aria-label="Large brand mark decoration area"></div>
    <div class="person">
      <div class="person-name">DWIGHT PENNER</div>
      <div class="person-title">CFO</div>
    </div>
    <p class="address">2170 Harbor Crest Lane<br>Costa Verde, CA 92600</p>
    <ul class="contacts">
      <li>555 318-0476
        <svg viewBox="0 0 24 24"><path d="M6.6 10.8a15 15 0 0 0 6.6 6.6l2.2-2.2a1 1 0 0 1 1-.25 11.4 11.4 0 0 0 3.6.57 1 1 0 0 1 1 1V20a1 1 0 0 1-1 1A17 17 0 0 1 3 4a1 1 0 0 1 1-1h3.5a1 1 0 0 1 1 1c0 1.25.2 2.45.57 3.6a1 1 0 0 1-.25 1z"/></svg>
      </li>
      <li>name@FALCRIDGE.com
        <svg viewBox="0 0 24 24"><path d="M2 5h20v14H2z M2 5l10 8 10-8" stroke="#fff" stroke-width="1.5"/></svg>
      </li>
      <li>www.FALCRIDGE.com
        <svg viewBox="0 0 24 24"><circle cx="12" cy="12" r="10"/></svg>
      </li>
    </ul>
  </section>
</body>
</html>
```